Corvane Systems Web Site

Need a complete redesign of the website to make it cleaner and up to date.
Current website: http://www.corvanesystems.example/
I am looking for a single page design focused on giving all the information about the POC (Pump Off Controller). And highlighting its benefits: Increased oil production, quick ROI, ease of use and low maintenance cost.
Here's a presentation of the product:
http://slidewharf.example/qk4mtz8vn2ra/?utm_campaign=share&utm_medium=copy&rc=ex0share
Please consider participating on the flyer design:
http://jobs.artmarket.example/job.aspx?id=391726
Here are some design examples of web sites I like:
http://www.bright-harbor.example/
I just added the source files for our business cards. I would like to see designs that incorporate the "tag cloud" on the back of the card..
Target Market(s)
Oil field decision makers. Engineers and technicians from 20 to 60.
Investors and venture capitalists.
Industry/Entity Type
Cleaner
Requirements
Must have
- Single page design
Nice to have
- Responsive web design

```html
<!DOCTYPE html>
<html lang="en">
<head>
<meta charset="utf-8">
<title>Corvane Systems</title>
<link href="https://fonts.googleapis.com/css2?family=Open+Sans:ital,wght@0,400;0,600;0,700;1,400&display=swap" rel="stylesheet">
<style>
:root{
  --red:#e2231a;
  --navy:#1f2a5a;
  --band:#3a3f9e;
  --ink:#333;
  --muted:#777;
  --light:#f2f2f2;
  --footer:#2b2b2b;
  --footer-deep:#1d1d1d;
  --footer-text:#c4c4c4;
  --yellow:#f7d417;
  --white:#fff;
}
*{margin:0;padding:0;box-sizing:border-box}
html,body{width:771px;height:1200px;overflow:hidden}
body{font-family:"Open Sans",Arial,sans-serif;color:var(--ink);background:#e9e9e9;position:relative;font-size:8px}
.page{position:absolute;left:0;top:0;width:771px;height:1200px;background:var(--white)}
.abs{position:absolute}

/* header */
.brand{left:85px;top:14px;display:flex;align-items:center;gap:7px;font-weight:700;font-size:19px;color:var(--red);letter-spacing:.5px}
.brand .dot{width:22px;height:22px;border-radius:50%;background:var(--red)}
.contact-top{left:400px;top:14px;font-size:8px;color:#555;display:flex;gap:14px;align-items:center;white-space:nowrap}
.contact-top span{display:flex;align-items:center;gap:4px}
.login{left:620px;top:10px;width:60px;height:18px;background:var(--red);color:var(--white);font-size:8px;font-weight:700;display:flex;align-items:center;justify-content:center;gap:4px}
.nav{left:300px;top:46px;display:flex;height:24px}
.nav a{color:#444;text-decoration:none;font-size:8px;font-weight:600;padding:0 14px;display:flex;align-items:center}
.nav a.active{background:var(--red);color:var(--white)}

/* hero */
.hero{left:0;top:85px;width:771px;height:218px;background:linear-gradient(180deg,#6f9ed0 0%,#a9c7e4 55%,#cfc6b0 78%,#8d7f63 100%)}
.hero-copy{left:154px;top:190px;width:330px}
.hero-copy p{display:inline;background:rgba(22,34,88,.88);color:var(--yellow);font-weight:700;font-size:12.5px;line-height:20px;padding:2px 6px;box-decoration-break:clone;-webkit-box-decoration-break:clone}

/* about + video */
h2.section-title{font-size:13px;font-weight:700;color:var(--navy);text-transform:uppercase}
.rule{height:2px;background:#ddd;position:relative}
.rule::before{content:"";position:absolute;left:0;top:0;width:40px;height:2px;background:var(--red)}
.about{left:85px;top:318px;width:340px}
.about .rule{margin:6px 0 10px}
.about p{font-size:7px;line-height:10.5px;color:#666;margin-bottom:7px}
.btn{display:inline-block;background:var(--red);color:var(--white);font-size:7px;font-weight:700;padding:4px 8px;text-transform:uppercase}
.video{left:452px;top:318px;width:229px}
.video .rule{margin:6px 0 10px}
.video-frame{width:229px;height:128px;position:relative;background:linear-gradient(180deg,#8fb4dc,#c7d6e4 60%,#7d6f55)}
.video-bar{position:absolute;left:0;bottom:0;width:100%;height:12px;background:rgba(0,0,0,.75);display:flex;align-items:center;padding:0 5px;gap:6px}
.video-bar .track{flex:1;height:2px;background:#888}

/* features */
.band{left:0;top:527px;width:771px;height:244px;background:var(--band)}
.card{top:548px;width:141px;height:196px;background:var(--white);text-align:center}
.card .photo{width:131px;height:82px;margin:5px auto 0;background:linear-gradient(180deg,#9dbbd9,#d3d7d6 60%,#8a7a5c)}
.card h3{font-size:8.5px;font-weight:600;color:#333;line-height:12px;margin:16px 8px 10px;height:24px}
.card .btn{font-size:6.5px}

/* feedback */
.feedback-title{left:0;top:826px;width:771px;text-align:center;font-size:13px;font-weight:700;color:var(--navy)}
.quote{left:85px;top:856px;width:596px;height:100px;background:var(--light)}
.quote .mark{position:absolute;left:12px;top:6px;font-size:32px;color:#bbb;font-family:Georgia,serif}
.quote p{position:absolute;left:40px;top:22px;width:470px;font-size:7.5px;line-height:12px;font-style:italic;color:#666}
.quote .who{position:absolute;right:18px;top:78px;font-size:7px;color:#555;font-weight:600}
.avatar{position:absolute;right:22px;top:12px;width:52px;height:52px;border-radius:50%;background:linear-gradient(180deg,#c9ced6,#9aa2ad);border:3px solid var(--white)}
.partners{left:85px;top:976px;width:596px;display:flex;justify-content:space-between}
.partners i{display:block;width:62px;height:20px;background:#d6d6d6;border-radius:3px}

/* footer */
.footer{left:0;top:1022px;width:771px;height:156px;background:var(--footer)}
.footer-col{color:var(--footer-text)}
.footer-col h4{color:var(--white);font-size:9px;font-weight:700;text-transform:uppercase;margin-bottom:10px}
.links{left:85px;top:1038px}
.links li{list-style:none;font-size:7.5px;line-height:13px;color:var(--footer-text)}
.links li::before{content:"›";color:var(--red);margin-right:5px}
.details{left:250px;top:1038px;width:180px}
.details div{display:flex;gap:6px;font-size:7.5px;line-height:11px;margin-bottom:6px;color:var(--footer-text)}
.details svg{flex:none;margin-top:1px}
.newsletter{left:520px;top:1030px;width:161px;height:138px;background:#3a3a3a;padding:10px}
.newsletter p{font-size:7px;line-height:10px;margin:-4px 0 8px;color:var(--footer-text)}
.field{height:14px;background:var(--white);margin-bottom:5px;font-size:7px;color:#999;display:flex;align-items:center;padding-left:5px}
.newsletter .btn{margin-top:2px}
.copyright{left:0;top:1178px;width:771px;height:22px;background:var(--footer-deep);color:#999;font-size:7px;display:flex;align-items:center;justify-content:center}
</style>
</head>
<body>
<div class="page">

  <header>
    <div class="abs brand"><span class="dot"></span>CORVANE</div>
    <div class="abs contact-top">
      <span><svg width="8" height="8" viewBox="0 0 10 10"><path d="M2 1l2 2-1 1.5c.7 1.3 1.7 2.3 3 3L7.5 6l2 2-1.5 1.5C4.5 9 1 5.5.5 2.5z" fill="#e2231a"/></svg>(555) 204-7718</span>
      <span><svg width="9" height="7" viewBox="0 0 10 8"><rect x=".5" y=".5" width="9" height="7" fill="none" stroke="#e2231a"/><path d="M.5.5L5 4.5 9.5.5" fill="none" stroke="#e2231a"/></svg>info@corvanesystems.example</span>
    </div>
    <div class="abs login"><svg width="7" height="8" viewBox="0 0 8 9"><rect x="1" y="4" width="6" height="5" fill="#fff"/><path d="M2 4V2.5a2 2 0 014 0V4" fill="none" stroke="#fff"/></svg>LOGIN</div>
    <nav class="abs nav">
      <a class="active">HOME</a><a>COMPANY</a><a>PRODUCTS</a><a>TELEMETRY</a><a>CONTACT US</a>
    </nav>
  </header>

  <section class="abs hero" role="img" aria-label="Oil pumpjack in a field under a blue sky"></section>
  <div class="abs hero-copy"><p>Are Your Well Running Under A Timer Switch? Have You Thought Of Increasing The Barrel Count At Each Well? Corvane Can Do It!</p></div>

  <section class="abs about">
    <h2 class="section-title">About Corvane</h2>
    <div class="rule"></div>
    <p>Our pump off controllers help operators keep every well running at its best, reading load and position on each stroke so the pump only runs when fluid is there to lift.</p>
    <p>Fewer dry strokes mean less wear on rods and motors, lower power bills and more barrels at each well. Setup is quick, the screens are simple, and our team stays close to support engineers and field technicians long after the first install.</p>
    <span class="btn">Read More</span>
  </section>

  <section class="abs video">
    <h2 class="section-title">Our Video</h2>
    <div class="rule"></div>
    <div class="video-frame" role="img" aria-label="Video still of pumpjacks at an oil field">
      <div class="video-bar"><svg width="6" height="6" viewBox="0 0 6 6"><path d="M0 0l6 3-6 3z" fill="#fff"/></svg><span class="track"></span></div>
    </div>
  </section>

  <section class="abs band"></section>
  <article class="abs card" style="left:85px"><div class="photo" role="img" aria-label="Pumpjack at a well site"></div><h3>High Reliability and Accessibility</h3><span class="btn">Read More</span></article>
  <article class="abs card" style="left:236px"><div class="photo" role="img" aria-label="Engineers reviewing reports at a desk"></div><h3>Alarm Generation and Reporting</h3><span class="btn">Read More</span></article>
  <article class="abs card" style="left:388px"><div class="photo" role="img" aria-label="Oil field equipment at sunset"></div><h3>Cost Savings due to Improved Pumper Efficiency</h3><span class="btn">Read More</span></article>
  <article class="abs card" style="left:540px"><div class="photo" role="img" aria-label="Row of pumpjacks on open land"></div><h3>Data Security</h3><span class="btn">Read More</span></article>

  <h2 class="abs feedback-title">CUSTOMER FEEDBACK</h2>
  <section class="abs quote">
    <span class="mark">&ldquo;</span>
    <p>Since we moved our wells onto these controllers the pumps run only when they should. Production went up within weeks, power costs came down, and our technicians spend far less time driving out to check on idle wells. The reports are clear and the alarms reach us fast, so small problems are fixed before they turn into costly failures in the field.</p>
    <div class="avatar" role="img" aria-label="Customer portrait"></div>
    <span class="who">Dale Hensley, Field Engineer, USA</span>
  </section>
  <div class="abs partners"><i></i><i></i><i></i><i></i><i></i><i></i><i></i><i></i></div>

  <footer class="abs footer"></footer>
  <div class="abs footer-col links">
    <h4>Quick Links</h4>
    <ul><li>Home</li><li>Company</li><li>Products</li><li>Telemetry</li><li>Contact Us</li></ul>
  </div>
  <div class="abs footer-col details">
    <h4>Contact Detail</h4>
    <div><svg width="7" height="9" viewBox="0 0 8 10"><path d="M4 0a4 4 0 014 4c0 3-4 6-4 6S0 7 0 4a4 4 0 014-4z" fill="#e2231a"/><circle cx="4" cy="4" r="1.5" fill="#2b2b2b"/></svg><span>418 Mesa Ridge Road, Suite 210<br>Alderton, TX 75012</span></div>
    <div><svg width="8" height="8" viewBox="0 0 10 10"><path d="M2 1l2 2-1 1.5c.7 1.3 1.7 2.3 3 3L7.5 6l2 2-1.5 1.5C4.5 9 1 5.5.5 2.5z" fill="#e2231a"/></svg><span>(555) 204-7718</span></div>
    <div><svg width="9" height="7" viewBox="0 0 10 8"><rect x=".5" y=".5" width="9" height="7" fill="none" stroke="#e2231a"/><path d="M.5.5L5 4.5 9.5.5" fill="none" stroke="#e2231a"/></svg><span>info@corvanesystems.example</span></div>
  </div>
  <div class="abs footer-col newsletter">
    <h4>Newsletter</h4>
    <p>Get valuable tips and news from Corvane. Sign up to our monthly newsletter today!</p>
    <div class="field">Name</div>
    <div class="field">Email</div>
    <span class="btn">Subscribe</span>
  </div>
  <div class="abs copyright">Copyright © 2014 - CORVANE</div>

</div>
</body>
</html>
```